Diverse, up-scale salon needs eye-catching, unique business cards.

We are looking for a unique business card design for our stylist but that can also be multi functional and used for appointment reminder and referrals. I will need a design in a format that I can modify names and titles going forward. In the past we have had a dark background with the logo on one side, and stylist and contact information on the other but we are open to all ideas. I have included our mission statement as well as branded colors below. The statement doesn't need to go on the card, it's just a reference for target market. We need space for the stylists name, title, instagram handle and then the salons phone number, website and address. I am also open to adding a spot for a qr code linked to the stylist instagram or the salon booking link.

primary brand colors:
#333333 #233415 #36502a #93874a #000000
Mission statement:
Vessolin Hair Studio, a high-end salon located in the lively Downtown Farmington, Michigan, is committed to providing exceptional services in a welcoming and relaxed environment to meet the needs of our diverse clientele.
Our salon specializes in contemporary custom haircuts, coloring, extensions, and barbering and beard grooming services. Our team of skilled stylists is passionate and inventive in their hair styling techniques. At the heart of our salon are values centered on quality, innovation, creativity, and above all, comfort. These core values are evident in every appointment across our customizable array of services.
Our goal is to establish a benchmark for exceptional hair care for every human.
Website: www.vessolinhairstudio.example
instagram: @vessolinhairstudio
address: 41782 Pelham Crest Rd, Farmington MI
phone: 248-613-4087

Industry/Entity Type

Hair Salon

Contact Information for Business Card

Stylist name, title, phone, instagram, website, address, (optional qr code)

Requirements
Should not have
• Does not need mission statement on the card.

```html
<!DOCTYPE html>
<html lang="en">
<head>
<meta charset="utf-8">
<title>Vessolin Hair Studio — Business Card</title>
<link href="https://fonts.googleapis.com/css2?family=Cinzel:wght@500&family=Montserrat:wght@400;500&display=swap" rel="stylesheet">
<style>
  :root {
    --backdrop: #3a3a3a;
    --card: #161616;
    --card-back: #121212;
    --gold: #93874a;
    --gold-soft: #a89a55;
    --ink: #f2f2f2;
    --pattern-dark: #0c0c0c;
    --pattern-light: #2a2a2a;
  }
  * { box-sizing: border-box; margin: 0; padding: 0; }
  html, body { width: 1200px; height: 801px; overflow: hidden; }
  body {
    background: var(--backdrop);
    display: flex;
    align-items: center;
    justify-content: center;
    gap: 40px;
    font-family: "Montserrat", sans-serif;
  }
  .card {
    position: relative;
    width: 520px;
    height: 298px;
    border: 2px solid var(--gold);
    overflow: hidden;
  }
  .card--front { background: var(--card); }
  .card--back { background: var(--card-back); }

  /* front */
  .brand-seal {
    position: absolute;
    top: 22px;
    right: 34px;
    width: 126px;
    height: 126px;
    border: 2px solid var(--gold);
    border-radius: 50%;
    display: flex;
    align-items: center;
    justify-content: center;
    text-align: center;
  }
  .brand-seal__name {
    font-family: "Cinzel", serif;
    font-weight: 500;
    color: var(--gold);
    font-size: 14px;
    line-height: 1.3;
    letter-spacing: 1px;
  }
  .divider {
    position: absolute;
    left: 36px;
    right: 20px;
    top: 176px;
    height: 1px;
    background: var(--gold);
  }
  .stylist {
    position: absolute;
    left: 36px;
    top: 116px;
  }
  .stylist__name {
    font-family: "Cinzel", serif;
    font-weight: 500;
    color: var(--gold-soft);
    font-size: 27px;
    letter-spacing: 1px;
    line-height: 1;
  }
  .stylist__title {
    color: var(--ink);
    font-size: 15px;
    margin-top: 8px;
  }
  .contact {
    position: absolute;
    left: 36px;
    top: 194px;
    list-style: none;
  }
  .contact__item {
    display: flex;
    align-items: center;
    gap: 10px;
    color: var(--ink);
    font-size: 14px;
    line-height: 25px;
  }
  .contact__icon { width: 13px; height: 13px; flex: none; }
  .address {
    position: absolute;
    right: 30px;
    top: 196px;
    text-align: right;
    color: var(--ink);
    font-size: 14px;
    line-height: 22px;
    font-style: normal;
  }

  /* back */
  .pattern-field {
    position: absolute;
    inset: 0;
    background: linear-gradient(110deg, var(--pattern-dark) 0%, var(--card-back) 45%, var(--pattern-light) 100%);
  }
  .back-mark {
    position: absolute;
    right: 40px;
    top: 50%;
    transform: translateY(-50%);
    font-family: "Cinzel", serif;
    font-weight: 500;
    font-size: 18px;
    color: var(--gold);
    letter-spacing: 1px;
  }
</style>
</head>
<body>
  <section class="card card--front" aria-label="Card front">
    <div class="brand-seal">
      <span class="brand-seal__name">Vessolin<br>Hair Studio</span>
    </div>

    <div class="stylist">
      <p class="stylist__name">MARISOL</p>
      <p class="stylist__title">President</p>
    </div>

    <div class="divider"></div>

    <ul class="contact">
      <li class="contact__item">
        <svg class="contact__icon" viewBox="0 0 16 16" aria-hidden="true"><path d="M3.5 1.5l3 3-1.6 1.6a9 9 0 0 0 5 5L11.5 9.5l3 3-2 2C6 14.5 1.5 10 1.5 3.5z" fill="var(--gold)"/></svg>
        248-613-4087
      </li>
      <li class="contact__item">
        <svg class="contact__icon" viewBox="0 0 16 16" aria-hidden="true"><circle cx="8" cy="8" r="6.5" fill="none" stroke="var(--gold)" stroke-width="1.6"/></svg>
        @vessolinhairstudio
      </li>
      <li class="contact__item">
        <svg class="contact__icon" viewBox="0 0 16 16" aria-hidden="true"><circle cx="8" cy="8" r="6.5" fill="none" stroke="var(--gold)" stroke-width="1.4"/><path d="M1.5 8h13M8 1.5c-3 3.5-3 9.5 0 13M8 1.5c3 3.5 3 9.5 0 13" fill="none" stroke="var(--gold)" stroke-width="1.2"/></svg>
        www.vessolinhairstudio.example
      </li>
    </ul>

    <address class="address">41782 Pelham Crest Rd<br>Farmington MI</address>
  </section>

  <section class="card card--back" aria-label="Card back">
    <div class="pattern-field" role="img" aria-label="Repeating embossed monogram pattern in glossy black fading to grey"></div>
    <span class="back-mark">Vessolin Hair Studio</span>
  </section>
</body>
</html>
```